ecommerce news podcast artwork

Podcast cover art for a podcast featuring daily news and events around ecommerce product businesses.

text to be: BRISK LOOP
optional third line of text with smaller font: Podcast

looking for something that pops with a medium to light blue background. text can be in white/red/orange colors. prefer solid colors for text, but background can vary.
I'm really open to other ideas too, sometimes you don't know what you want until you see it.

Target Market(s)

ecommerce business owners, managers

Industry/Entity Type

news, business, ecommerce

Font styles to use
Sans Serif

Colors
0054AA
0677BA
7BADD7
CADEEF
E8F1F8
0094D4
00A9DD
6FCCEA
C7EBF8
E9F6FB
F0912C
F2A743
F7CA91
FBE8D2
FDF5EE
EB3D1F
EC4F4E
F09395
F8D3D4
FCEDEE

Requirements
Must have
• text: BRISK LOOP
Should not have
• no microphones, headsets/headphones, speakers, or other props like that.

```html
<!DOCTYPE html>
<html lang="en">
<head>
<meta charset="utf-8">
<title>Brisk Loop Podcast</title>
<link rel="stylesheet" href="https://fonts.googleapis.com/css2?family=Titan+One&family=Montserrat:wght@500&display=swap">
<style>
  :root {
    --sky-edge: #6FCCEA;
    --sky-mid: #C7EBF8;
    --sky-center: #FFFFFF;
    --ink: #27212B;
    --signal-red: #EA3C1F;
  }
  html, body {
    margin: 0;
    padding: 0;
    overflow: hidden;
    background: var(--sky-mid);
  }
  .cover {
    position: relative;
    width: 1200px;
    height: 1200px;
    overflow: hidden;
  }
  .cover__burst {
    position: absolute;
    inset: 0;
    background: radial-gradient(circle at 50% 52%, var(--sky-center) 0%, var(--sky-center) 12%, var(--sky-mid) 48%, var(--sky-edge) 100%);
  }
  .cover__title {
    position: absolute;
    inset: 0;
    width: 1200px;
    height: 1200px;
  }
  .title__line {
    font-family: "Titan One", sans-serif;
  }
  .title__line--top { fill: var(--ink); }
  .title__line--bottom { fill: var(--signal-red); }
  .cover__label {
    position: absolute;
    left: 0;
    right: 0;
    top: 952px;
    text-align: center;
    font-family: "Montserrat", sans-serif;
    font-weight: 500;
    font-size: 54px;
    letter-spacing: 0.22em;
    color: var(--ink);
    padding-left: 0.22em;
  }
</style>
</head>
<body>
  <main class="cover">
    <div class="cover__burst" role="img" aria-label="Light blue sunburst rays radiating from a bright white centre"></div>
    <svg class="cover__title" viewBox="0 0 1200 1200" aria-label="BRISK LOOP">
      <text class="title__line title__line--top" x="212" y="547" font-size="250" textLength="762" lengthAdjust="spacingAndGlyphs">BRISK</text>
      <text class="title__line title__line--bottom" x="143" y="842" font-size="372" textLength="920" lengthAdjust="spacingAndGlyphs">LOOP</text>
    </svg>
    <p class="cover__label">PODCAST</p>
  </main>
</body>
</html>
```